At Home Pet Euthanasia - business cards & brand stationary

We already have a logo and the colors and a website. Need a business card designed that will be able to customized to multiple veterinarians who will be partnering with us. The feel needs to be compassionate, comforting with our tagline 'A Gift of Love at Home'. It will be 2 sides.
On the back our platform/partner vets will be customizing each business card with their own service areas, phone numbers, name and title. On the front, i would like to see experimentation with use of our photos, the logo, tagline and a description 'Peaceful and Compassionate At-Home Pet Euthanasia'

```html
<!DOCTYPE html>
<html lang="en">
<head>
<meta charset="utf-8">
<title>Lumenpaw Business Cards</title>
<link href="https://fonts.googleapis.com/css2?family=Poppins:wght@300;400;500;600;700&family=Arimo:wght@400&display=swap" rel="stylesheet">
<style>
  :root {
    --page-bg: #1e1e1e;
    --brand-blue: #7896bf;
    --brand-blue-soft: #a9bdd8;
    --card-white: #ffffff;
    --front-bg: #eef3f9;
    --ink: #1a1a1a;
    --rule: #b5b5b5;
  }
  * { box-sizing: border-box; margin: 0; padding: 0; }
  html, body { width: 1200px; height: 1015px; overflow: hidden; }
  body {
    background: var(--page-bg);
    font-family: "Poppins", sans-serif;
    display: flex;
    flex-direction: column;
    align-items: center;
    justify-content: center;
    gap: 56px;
  }
  .card {
    width: 640px;
    height: 366px;
    position: relative;
    overflow: hidden;
    box-shadow: 0 12px 30px rgba(0,0,0,.55);
  }

  /* Front */
  .card-front { background: linear-gradient(90deg, #f4f8fc 0%, var(--front-bg) 60%, #e4ecf5 100%); }
  .photo-area {
    position: absolute;
    right: 0; top: 0;
    width: 44%; height: 100%;
    background:
      radial-gradient(ellipse 60% 62% at 55% 50%, #1c2230 0%, #2a3244 45%, rgba(42,50,68,0) 78%),
      linear-gradient(90deg, rgba(228,236,245,0) 0%, #dfe7f1 100%);
  }
  .front-brand {
    position: absolute;
    left: 40px; bottom: 78px;
  }
  .brand-row { display: flex; align-items: center; gap: 14px; }
  .brand-dot {
    width: 46px; height: 46px; border-radius: 50%;
    background: var(--brand-blue);
    flex: none;
  }
  .brand-name {
    font-weight: 600;
    color: var(--brand-blue);
    font-size: 38px;
    line-height: 1;
    letter-spacing: .3px;
  }
  .front-tagline {
    margin: 8px 0 0 60px;
    font-weight: 300;
    font-size: 16px;
    color: var(--brand-blue-soft);
    letter-spacing: .6px;
  }

  /* Back */
  .card-back { background: var(--card-white); }
  .back-brand {
    position: absolute;
    left: 0; top: 92px;
    width: 352px;
    display: flex; flex-direction: column; align-items: center; gap: 12px;
  }
  .back-brand .brand-dot { width: 84px; height: 84px; }
  .back-brand .brand-name { font-size: 46px; }
  .divider {
    position: absolute;
    left: 352px; top: 42px;
    width: 1px; height: 210px;
    background: var(--rule);
  }
  .contact {
    position: absolute;
    left: 380px; top: 44px;
    color: var(--ink);
    font-family: "Arimo", sans-serif;
  }
  .person-name {
    font-family: "Poppins", sans-serif;
    font-weight: 600;
    color: var(--brand-blue);
    font-size: 25px;
    line-height: 1.1;
  }
  .person-title { font-size: 16px; margin-bottom: 18px; }
  .contact-list { list-style: none; font-size: 16px; line-height: 1.55; }
  .contact-list li { display: flex; align-items: center; gap: 8px; }
  .contact-list svg { width: 15px; height: 15px; flex: none; }
  .accent { color: var(--brand-blue); }
  .address { margin: 14px 0 0 23px; font-size: 16px; line-height: 1.4; }
  .service-band {
    position: absolute;
    left: 0; bottom: 0;
    width: 100%; height: 56px;
    background: var(--brand-blue);
    color: #fff;
    font-weight: 500;
    font-size: 19px;
    letter-spacing: .6px;
    display: flex; align-items: center; justify-content: center;
  }
</style>
</head>
<body>

  <section class="card card-front">
    <div class="photo-area" role="img" aria-label="Portrait photo of a senior black dog wearing a pale blue collar against a light background"></div>
    <div class="front-brand">
      <div class="brand-row">
        <span class="brand-dot"></span>
        <span class="brand-name">Lumenpaw</span>
      </div>
      <p class="front-tagline">A gift of love at home.</p>
    </div>
  </section>

  <section class="card card-back">
    <div class="back-brand">
      <span class="brand-dot"></span>
      <span class="brand-name">Lumenpaw</span>
    </div>
    <div class="divider"></div>
    <div class="contact">
      <p class="person-name">Daniel Hart</p>
      <p class="person-title">Managing Director</p>
      <ul class="contact-list">
        <li>
          <svg viewBox="0 0 16 16"><path d="M3.5 1.5l2.5 3-1.5 1.5c.8 2 2.5 3.7 4.5 4.5L10.5 9l3 2.5-1.5 2.5C6.5 13.5 2.5 9.5 1 4z" fill="var(--brand-blue)"/></svg>
          055-210 384 617
        </li>
        <li>
          <svg viewBox="0 0 16 16"><rect x="1" y="3" width="14" height="10" fill="var(--brand-blue)"/><path d="M1 3l7 6 7-6" stroke="#fff" stroke-width="1.4" fill="none"/></svg>
          hello@lumenpaw.com
        </li>
        <li>
          <svg viewBox="0 0 16 16"><circle cx="8" cy="8" r="6.5" fill="none" stroke="var(--brand-blue)" stroke-width="1.5"/><ellipse cx="8" cy="8" rx="3" ry="6.5" fill="none" stroke="var(--brand-blue)" stroke-width="1.2"/><path d="M1.5 8h13" stroke="var(--brand-blue)" stroke-width="1.2"/></svg>
          <span>www.<span class="accent">lumenpaw</span>.com</span>
        </li>
      </ul>
      <p class="address">18, Willow Lane, Suite 4<br>30218, Country Name</p>
    </div>
    <div class="service-band">Peaceful and Compassionate At-Home Pet Euthanasia</div>
  </section>

</body>
</html>
```